4th Generation Family Business Needs a New Card Design!

We are a family owned 4th Generation company. We are based in the Sydney, Australia area and we are desperately in need of a more modern and classy card. We are monumental masons who design, supply & erect lasting memorials throughout cemeteries in Sydney. Our customers are normally in a period of grieving. I have attached logo files that will need to be implemented on the card. Company was established 1935. Australian Owned and Operated. Card needs to be designed to PIXO.com specification.

Target Market(s)

Our target market is based upon people that a grieving for family members that have passed away. We also deal with alot of companies that own and operate cemeteries.

Industry/Entity Type

Business

Contact Information for Business Card

Simon Harcourt, Operations Manager, 0417293086, simon@harcourtmemorials.com.au
Lewis Harcourt, Director, 0491630572, lewis@harcourtmemorials.com.au
Phone # 02 9561 3048
Website: www.harcourtmemorials.com.au
Address: Suite 17, 8 Palfrey Lane, West Carlow, Sydney NSW 2156

Font styles to use
Serif
Decorative
Script

Requirements
Must have
• Would like to see the logo nicely implemented with a modern design. Embossed lettering would be a nice additive.

```html
<!DOCTYPE html>
<html lang="en">
<head>
<meta charset="utf-8">
<title>Harcourt Memorials – Business Card</title>
<link rel="stylesheet" href="https://fonts.googleapis.com/css2?family=Cinzel:wght@400;600&family=Open+Sans:ital,wght@0,400;1,400&display=swap">
<style>
  :root {
    --backdrop: #8c8c8c;
    --card-light: #f1f1f1;
    --card-dark: #221e1b;
    --ink: #1f1f1f;
    --ink-soft: #3a3a3a;
    --gold: #c9a227;
    --white: #f4f4f4;
  }
  * { margin: 0; padding: 0; box-sizing: border-box; }
  html, body {
    width: 1105px; height: 1200px; overflow: hidden;
    background: var(--backdrop);
  }
  .card {
    position: absolute; left: 184px; width: 744px; height: 425px; overflow: hidden;
  }
  .card--front { top: 120px; background: var(--card-light); }
  .card--back { top: 637px; background: var(--card-dark); }

  .monogram-watermark {
    position: absolute; left: 320px; top: 0; width: 380px; height: 425px;
    background: linear-gradient(180deg, rgba(170,170,170,.35), rgba(225,215,185,.35));
  }
  .brand-name {
    position: absolute; left: 41px; top: 118px; width: 260px;
    font-family: "Cinzel", serif; font-weight: 600; color: var(--ink);
    font-size: 30px; line-height: 1.05; letter-spacing: .5px;
  }
  .rule {
    position: absolute; left: 44px; top: 196px; width: 656px; height: 2px; background: var(--gold);
  }
  .person {
    position: absolute; right: 44px; top: 128px; text-align: right;
  }
  .person__name {
    font-family: "Cinzel", serif; font-weight: 600; font-size: 26px; color: var(--ink); letter-spacing: 1px;
  }
  .person__role {
    font-family: "Open Sans", sans-serif; font-size: 18px; color: var(--gold); margin-top: -2px;
  }
  .accent-bar {
    position: absolute; right: 0; top: 132px; width: 14px; height: 52px; background: var(--gold);
  }
  .contact-list, .address {
    position: absolute; top: 278px; list-style: none;
    font-family: "Open Sans", sans-serif; font-size: 18px; color: var(--ink-soft); line-height: 28.5px;
  }
  .contact-list { left: 44px; }
  .contact-list li { display: flex; align-items: center; gap: 10px; }
  .contact-list svg { width: 16px; height: 16px; fill: var(--ink); flex: none; }
  .address { right: 44px; text-align: right; font-style: normal; }

  .pattern-field {
    position: absolute; inset: 0;
    background: linear-gradient(180deg, #2a2622, #1d1a17);
  }
  .back-brand {
    position: absolute; left: 0; right: 0; top: 150px; text-align: center;
    font-family: "Cinzel", serif; font-weight: 400; color: var(--white);
    font-size: 58px; line-height: 1; letter-spacing: 1px;
  }
  .back-brand span { display: block; font-size: 30px; letter-spacing: 3px; margin-top: 10px; }
  .back-web {
    position: absolute; left: 0; right: 0; top: 272px; text-align: center;
    font-family: "Open Sans", sans-serif; font-style: italic; font-size: 18px;
    letter-spacing: 3px; color: var(--white);
  }
</style>
</head>
<body>
  <section class="card card--front">
    <div class="monogram-watermark" role="img" aria-label="Faint large company monogram"></div>
    <div class="brand-name">Harcourt<br>Memorials</div>
    <div class="rule"></div>
    <div class="person">
      <div class="person__name">Simon Harcourt</div>
      <div class="person__role">Operations Manager</div>
    </div>
    <div class="accent-bar"></div>
    <ul class="contact-list">
      <li><svg viewBox="0 0 16 16"><path d="M3 1l3 3-1.5 2c1 2 3 4 5 5L11.5 9.5l3 3L13 15C7 15 1 9 1 3z"/></svg>02 9561 3048</li>
      <li><svg viewBox="0 0 16 16"><path d="M4 0h8a1 1 0 0 1 1 1v14a1 1 0 0 1-1 1H4a1 1 0 0 1-1-1V1a1 1 0 0 1 1-1zm1 2v10h6V2zm3 11a1 1 0 1 0 0 2 1 1 0 0 0 0-2z"/></svg>0417293086</li>
      <li><svg viewBox="0 0 16 16"><path d="M1 3h14v10H1zm1 1.2V12h12V4.2L8 9z"/><path d="M1 3l7 5.5L15 3z"/></svg>simon@harcourtmemorials.com.au</li>
      <li><svg viewBox="0 0 16 16"><circle cx="8" cy="8" r="7"/></svg>www.harcourtmemorials.com.au</li>
    </ul>
    <address class="address">
      Suite 17<br>8 Palfrey Lane<br>West Carlow<br>Sydney NSW 2156
    </address>
  </section>

  <section class="card card--back">
    <div class="pattern-field" role="img" aria-label="Repeating company monogram pattern in dark tones"></div>
    <div class="back-brand">HARCOURT<span>MEMORIALS</span></div>
    <div class="back-web">www.harcourtmemorials.com.au</div>
  </section>
</body>
</html>
```